full stationary design for a modern sleek design company

we are a design company that does modern minimalistic interior design works as well as other design services for high end clients.
we need a full stationary design including and not limited to (double sided business card, letter head, envelopes, documents folder...etc) that reflects the modern style design we do.
sleek modern and minimalistic is the requirements.
Updates

please use the latest attached files as there was a slight modification on the logo Added Wednesday, March 1, 2017

minor update on the logo files in JPG and PSD has been updated kindly follow the new attachments. Added Thursday, March 2, 2017

Target Market(s)

modern minimalist clients

Industry/Entity Type

Design Agency

Requirements
Must have
• the logo
Nice to have
• i like the colors in the colored 3D logo attached
Should not have
• too many colors

```html
<!DOCTYPE html>
<html lang="en">
<head>
<meta charset="utf-8">
<title>Vale Design Studio – Business Card</title>
<link rel="stylesheet" href="https://fonts.googleapis.com/css2?family=Lato:wght@300;400;700;900&display=swap">
<style>
  :root {
    --backdrop: #e4e4e4;
    --card-dark: #3a3a3a;
    --card-dark-edge: #2c2c2c;
    --card-light: #ffffff;
    --accent: #f7a12b;
    --ink-light: #ffffff;
    --ink-soft: #d6d6d6;
    --ink-dark: #4a4a4a;
  }
  * { box-sizing: border-box; margin: 0; padding: 0; }
  html, body {
    width: 1200px;
    height: 695px;
    overflow: hidden;
    background: var(--backdrop);
    font-family: "Lato", sans-serif;
  }
  .canvas {
    position: relative;
    width: 1200px;
    height: 695px;
  }
  .card {
    position: absolute;
    top: 199px;
    width: 520px;
    height: 297px;
    box-shadow: 0 6px 18px rgba(0,0,0,0.18);
    overflow: hidden;
  }
  /* Front */
  .card-front {
    left: 55px;
    background: linear-gradient(135deg, #474747 0%, var(--card-dark) 50%, var(--card-dark-edge) 100%);
    display: flex;
    align-items: center;
    justify-content: center;
  }
  .brand {
    display: flex;
    align-items: center;
    gap: 14px;
  }
  .brand-square {
    width: 30px;
    height: 30px;
    background: var(--accent);
  }
  .brand-text { display: flex; flex-direction: column; }
  .brand-name {
    color: var(--ink-light);
    font-weight: 700;
    font-size: 30px;
    letter-spacing: 1.5px;
    line-height: 1;
  }
  .brand-tagline {
    margin-top: 6px;
    color: var(--accent);
    font-weight: 400;
    font-size: 12px;
    letter-spacing: 4.6px;
  }
  /* Back */
  .card-back {
    left: 625px;
    display: flex;
  }
  .back-logo-panel {
    width: 47%;
    background: var(--card-light);
    display: flex;
    align-items: center;
    justify-content: center;
    gap: 10px;
  }
  .back-logo-panel .brand-square { width: 22px; height: 22px; }
  .back-logo-name {
    color: var(--ink-dark);
    font-weight: 700;
    font-size: 26px;
    letter-spacing: 1px;
  }
  .back-info-panel {
    width: 53%;
    background: linear-gradient(135deg, #454545 0%, var(--card-dark) 60%, var(--card-dark-edge) 100%);
    padding: 74px 0 0 26px;
    color: var(--ink-soft);
  }
  .person-name {
    color: var(--ink-light);
    font-size: 17px;
    letter-spacing: 1px;
    line-height: 1;
  }
  .person-name .given { font-weight: 900; }
  .person-name .family { font-weight: 300; }
  .person-role {
    color: var(--accent);
    font-size: 10.5px;
    margin-top: 4px;
  }
  .address {
    font-size: 10.5px;
    line-height: 1.45;
    margin-top: 16px;
    font-style: normal;
  }
  .contact {
    list-style: none;
    font-size: 10.5px;
    line-height: 1.45;
    margin-top: 16px;
    padding-left: 8px;
    border-left: 2px solid var(--accent);
  }
</style>
</head>
<body>
<main class="canvas">
  <section class="card card-front" aria-label="Business card front">
    <div class="brand">
      <span class="brand-square"></span>
      <div class="brand-text">
        <span class="brand-name">VALE DESIGN STUDIO</span>
        <span class="brand-tagline">BY ELIAS VARN</span>
      </div>
    </div>
  </section>

  <section class="card card-back" aria-label="Business card back">
    <div class="back-logo-panel">
      <span class="brand-square"></span>
      <span class="back-logo-name">VALE</span>
    </div>
    <div class="back-info-panel">
      <p class="person-name"><span class="given">LENA</span> <span class="family">HART</span></p>
      <p class="person-role">Graphic Designer</p>
      <address class="address">48 Alder Row<br>Westbrook NY 10000</address>
      <ul class="contact">
        <li>000. 5550. 1234</li>
        <li>hello@valestudio.com</li>
        <li>www.valestudio.com</li>
      </ul>
    </div>
  </section>
</main>
</body>
</html>
```